SkyvoTrade - where frequent flyers can cash out their airline miles

SkyvoTrade enable the trade of airline miles between individuals. Our landing page which I want to redesign should refer to individuals who have miles in airline loyalty programs and would like to sell them with our platform

I would like to get a landing page design with a look and feel much more advanced and appealing then the one we currently have.

Page should include the information and fields in our current landing page but should be more professional and include except for the current two partner's logos and our logo of course, also the attached banner of staynestly.example with a link to staynestly.example with our affiliate code.

Audience of our web page is business men and heavy travellers therefore, page should reflect professionalism and should be business wise. There could be something that has to do with airplanes and money in terms of the background and pictures shows.

Additional text (on top of the short description at skyvotrade.example is -
"
SkyvoTrade™ converts frequent flyers' accumulated miles to exceptionally low-priced flight tickets. It serves as an online trading platform for sellers of miles and buyers of flight tickets, offering airline customers a fully automated process whereby flight tickets are created out of loyalty club miles.
"

Our web site as a reference is www.skyvotrade.example

Target Market(s)

Business men who are heavily travellers

Industry/Entity Type

Travel Industry

Number of Pages Required

1 page

Font styles to use
Sans Serif

Colors
85acd3
0255a3

Requirements
Must have
• Our logo and the 3 logos mentioned at the description. It should have on the top the look & Feel that it currently has on our landing page - www.skyvotrade.example
Nice to have
• I would like people entering the web page to love it and for them to leave the relevant details so we get back to them
Should not have
• Not too many texts or images. Don't want people to scroll down too much if at all

```html
<!DOCTYPE html>
<html lang="en">
<head>
<meta charset="utf-8">
<title>SkyvoTrade – Loyalty Pays</title>
<link href="https://fonts.googleapis.com/css2?family=Open+Sans:wght@400;600;700&family=Arimo:wght@400;700&display=swap" rel="stylesheet">
<style>
:root{
  --navy:#0255a3;
  --sky:#85acd3;
  --ink:#222;
  --grey-bg:#e6e9ee;
  --rule:#cfd4db;
  --white:#fff;
}
*{box-sizing:border-box;margin:0;padding:0}
html,body{width:899px;height:1200px;overflow:hidden;background:var(--white)}
body{font-family:"Arimo",Arial,sans-serif;color:var(--ink);position:relative}

/* header */
.site-header{position:absolute;top:0;left:0;width:899px;height:83px;background:var(--white)}
.brand{position:absolute;left:83px;top:18px}
.brand-name{font-family:"Open Sans",Arial,sans-serif;font-weight:700;font-size:26px;color:#1a1a1a;letter-spacing:-.5px;line-height:30px;display:flex;align-items:center;gap:6px}
.brand-name .mark{width:14px;height:14px;background:var(--navy);display:inline-block}
.brand-tag{font-family:"Arimo",sans-serif;font-weight:700;font-size:9px;text-align:right;margin-top:3px;color:#111}
.contact{position:absolute;left:524px;top:26px;display:flex;gap:8px}
.contact-text .call{font-size:11.5px;color:#333;line-height:20px}
.contact-text .call b{font-weight:400;font-size:15px;color:var(--navy)}
.contact-text .sub{font-size:8px;color:#888}
.signup-btn{position:absolute;left:722px;top:26px;width:93px;height:32px;border-radius:16px;background:var(--navy);color:var(--white);font-family:"Open Sans",sans-serif;font-weight:600;font-size:10.5px;display:flex;align-items:center;justify-content:center;gap:4px}

/* hero */
.hero{position:absolute;top:83px;left:0;width:899px;height:549px;background:linear-gradient(180deg,#0a4d9e 0%,#1d8ef2 45%,#0b5bb0 75%,#0355a5 100%)}
.slider{position:absolute;left:84px;top:15px;width:731px;height:335px;border:1px solid rgba(255,255,255,.7);
  background:
    radial-gradient(ellipse 60% 22% at 30% 92%,rgba(255,255,255,.95),rgba(255,255,255,0) 70%),
    radial-gradient(ellipse 55% 20% at 75% 88%,rgba(255,255,255,.9),rgba(255,255,255,0) 70%),
    radial-gradient(ellipse 38% 12% at 57% 42%,rgba(240,246,252,.55),rgba(240,246,252,0) 75%),
    linear-gradient(180deg,#13335f 0%,#24589a 22%,#3f86cf 45%,#7fb4e4 62%,#c9def1 76%,#eef3f8 88%,#d3dfec 100%);
  box-shadow:0 16px 24px -10px rgba(0,0,40,.45)}
.slide-caption{position:absolute;left:96px;top:214px;width:538px;height:58px;background:rgba(235,242,250,.55);display:flex;align-items:center;justify-content:center;font-size:15.5px;color:var(--navy)}
.dots{position:absolute;top:310px;left:345px;display:flex;gap:5px}
.dots span{width:8px;height:8px;border-radius:50%;background:#888}
.dots span.on{background:var(--navy)}
.welcome{position:absolute;top:395px;left:84px;width:731px;text-align:center;color:var(--white)}
.welcome h1{font-family:"Open Sans",sans-serif;font-weight:600;font-size:20px;letter-spacing:.3px}
.welcome p{font-size:8.2px;line-height:19px;margin-top:8px}
.sell-btn{position:absolute;left:384px;top:481px;width:131px;height:33px;border-radius:17px;background:linear-gradient(#fff,#dbe4ee);color:var(--navy);font-family:"Open Sans",sans-serif;font-size:10px;display:flex;align-items:center;justify-content:center;gap:4px;box-shadow:0 2px 4px rgba(0,0,0,.25)}

/* feature cards */
.features{position:absolute;top:632px;left:0;width:899px;height:197px;background:var(--white)}
.card{position:absolute;top:23px;width:230px;height:142px;border:1px solid #cdd6e0;box-shadow:0 12px 12px -8px rgba(0,0,0,.35);overflow:hidden}
.card-photo{position:absolute;inset:0}
.photo-terminal{background:
  linear-gradient(152deg,rgba(255,255,255,0) 52%,#5d8ec5 53%,#2f63a3 62%,rgba(47,99,163,0) 63%),
  linear-gradient(180deg,#1f5fb0 0%,#4f8fd8 35%,#a8cbef 65%,#e6eff8 80%,#6f93bd 100%)}
.photo-tower{background:
  linear-gradient(90deg,rgba(0,0,0,0) 60%,#6f8092 61%,#a9b7c6 75%,#58687a 100%),
  linear-gradient(180deg,#3e8ee0 0%,#7fb3e8 55%,#a9c8e8 75%,#6b7b8e 100%)}
.photo-clouds{background:
  radial-gradient(ellipse 70% 30% at 40% 78%,rgba(255,255,255,.9),rgba(255,255,255,0) 70%),
  linear-gradient(180deg,#2a69b6 0%,#79a9dc 40%,#cfe0f1 65%,#eef3f8 80%,#4a7fb8 100%)}
.card-label{position:absolute;left:0;right:0;bottom:0;height:41px;background:rgba(2,85,163,.82);color:var(--white);font-family:"Open Sans",sans-serif;font-weight:600;font-size:11.5px;padding:12px 0 0 22px}

/* info */
.info{position:absolute;top:829px;left:0;width:899px;height:315px;background:var(--grey-bg)}
.promo{position:absolute;left:84px;top:27px;width:161px;height:103px;border:1px solid #c5ccd5;background:linear-gradient(180deg,#1f4f99 0%,#7d7fc0 45%,#e2806a 75%,#3b5f9a 100%)}
.promo-title{font-family:"Open Sans",sans-serif;font-weight:600;font-size:8.4px;color:var(--white);text-align:center;margin-top:10px}
.promo-name{font-family:"Open Sans",sans-serif;font-weight:700;font-size:13px;color:var(--white);text-align:center;margin-top:2px}
.promo-btn{position:absolute;left:39px;top:67px;width:84px;height:25px;border-radius:13px;background:var(--navy);color:var(--white);font-size:7.5px;display:flex;align-items:center;justify-content:center;gap:3px}
.promo-copy{position:absolute;left:260px;top:34px;width:304px}
.promo-copy h2{font-family:"Open Sans",sans-serif;font-weight:700;font-size:14px;color:#3d4a5c}
.promo-copy p{font-size:8.3px;line-height:19.2px;color:#777;text-align:justify;margin-top:2px}
.partners{position:absolute;left:584px;top:48px;width:231px;display:flex;justify-content:space-between;align-items:center}
.partner{display:flex;align-items:center;gap:5px;font-family:"Open Sans",sans-serif;font-weight:600;font-size:12px;color:#4a5563}
.partner i{width:20px;height:20px;background:#4a5563;display:inline-block}
.partner.red{color:#c8171d}
.partner.red i{background:#c8171d;border-radius:50%}
.rule{position:absolute;height:1px;background:var(--rule)}
.side-title{position:absolute;left:584px;font-family:"Open Sans",sans-serif;font-weight:600;font-size:11.5px;color:#2b2f36}
.socials{position:absolute;left:584px;top:137px;display:flex;gap:8px}
.socials span{width:27px;height:26px;border-radius:4px;display:flex;align-items:center;justify-content:center}
.newsletter{position:absolute;left:584px;top:226px;width:231px;height:34px;border:1px solid #c9ced6;background:#eceef1;font-size:8.8px;color:#999;padding:0 0 0 11px;display:flex;align-items:center}
.newsletter .go{position:absolute;right:8px;top:4px;width:26px;height:26px;border-radius:50%;background:var(--navy);display:flex;align-items:center;justify-content:center}
.links{position:absolute;top:172px}
.links h3{font-family:"Open Sans",sans-serif;font-weight:600;font-size:11.5px;color:#2b2f36;margin-bottom:8px}
.links li{list-style:none;font-size:8.3px;color:#666;height:25.7px;display:flex;align-items:center;gap:4px}

/* footer */
.site-footer{position:absolute;top:1144px;left:0;width:899px;height:56px;background:var(--navy);color:var(--white);font-size:8.8px}
.site-footer .copy{position:absolute;left:83px;top:23px}
.site-footer .legal{position:absolute;right:83px;top:23px}
</style>
</head>
<body>

<header class="site-header">
  <div class="brand">
    <div class="brand-name"><span class="mark"></span>SkyvoTrade</div>
    <div class="brand-tag">Loyalty Pays</div>
  </div>
  <div class="contact">
    <svg width="28" height="28" viewBox="0 0 28 28" aria-hidden="true"><circle cx="14" cy="14" r="12.5" fill="none" stroke="#0255a3" stroke-width="1.6"/><path d="M9 8c1-1 2-1 2.6 0l1.4 2.3c.4.7.2 1.3-.4 1.8l-.9.7c.8 1.8 2 3 3.7 3.8l.7-.9c.5-.6 1.1-.8 1.8-.4l2.3 1.4c1 .6 1 1.6 0 2.6-1.4 1.4-3 1.5-5 .4-3-1.7-5-4-6.5-6.8-1-2-.9-3.5.3-4.9z" fill="#0255a3"/></svg>
    <div class="contact-text">
      <div class="call">Call Us <b>123 456 789 00</b></div>
      <div class="sub">Lorem ipsum dolor sit amet, consectetur</div>
    </div>
  </div>
  <div class="signup-btn"><svg width="10" height="10" viewBox="0 0 10 10" aria-hidden="true"><circle cx="5" cy="5" r="5" fill="#fff"/><path d="M5 2.5v5M2.5 5h5" stroke="#0255a3" stroke-width="1.5"/></svg>SIGN UP</div>
</header>

<section class="hero">
  <div class="slider" role="img" aria-label="Photo: white passenger jet airliner flying above a bright sea of clouds under a deep blue sky">
    <div class="slide-caption">Online trading platform for sellers of miles and buyers of Flight Tickets</div>
    <div class="dots"><span></span><span></span><span class="on"></span><span></span></div>
  </div>
  <div class="welcome">
    <h1>WELCOME TO SKYVOTRADE</h1>
    <p>SkyvoTrade™ converts frequent flyers' accumulated miles to exceptionally low-priced flight tickets. It serves as an online trading platform for sellers of miles and buyers of flight tickets, offering airline customers a fully automated process whereby flight tickets are created out of loyalty club miles.</p>
  </div>
  <div class="sell-btn"><svg width="11" height="10" viewBox="0 0 11 10" aria-hidden="true"><path d="M0 1v3.5L5 9.5 9 5.5 4 .5H.5z" fill="#0255a3"/><circle cx="2.2" cy="2.4" r=".8" fill="#fff"/></svg>SELL YOUR MILES</div>
</section>

<section class="features">
  <div class="card" style="left:84px">
    <div class="card-photo photo-terminal" role="img" aria-label="Photo: airliner climbing past a modern terminal roof against a blue sky"></div>
    <div class="card-label">LOW-PRICED FLIGHT TICKETS</div>
  </div>
  <div class="card" style="left:334px">
    <div class="card-photo photo-tower" role="img" aria-label="Photo: airport control tower beside a glass terminal building"></div>
    <div class="card-label">ONLINE TRADING PLATFORM</div>
  </div>
  <div class="card" style="left:585px">
    <div class="card-photo photo-clouds" role="img" aria-label="Photo: jet airliner flying over white clouds"></div>
    <div class="card-label">LATEST OFFERS</div>
  </div>
</section>

<section class="info">
  <div class="promo" role="img" aria-label="Staynestly banner showing a pier stretching into a sunset sea">
    <div class="promo-title">NEW DEALS LISTED EVERY DAY</div>
    <div class="promo-name">Staynestly</div>
    <div class="promo-btn"><svg width="8" height="8" viewBox="0 0 8 8" aria-hidden="true"><rect x=".5" y="1.5" width="7" height="6" fill="none" stroke="#fff"/><path d="M.5 3h7M2.5 0v2M5.5 0v2" stroke="#fff"/></svg>BOOK NOW</div>
  </div>
  <div class="promo-copy">
    <h2>Staynestly</h2>
    <p>Lorem ipsum dolor sit amet, consectetur adipiscing elit. Morbi et elit ut diam bibendum dictum eget ut nisi. Etiam tristique euismod maximus. Nulla feugiat magna at odio pellentesque, a fermentum felis maximus. Nam congue tortor id dignissim maximus. Ut in ultricies erat. Aenean ac sagittis dolor.</p>
  </div>

  <div class="partners">
    <div class="partner"><i></i>Brightgrid Labs</div>
    <div class="partner red"><i></i>Orvalen Tours</div>
  </div>
  <div class="rule" style="left:584px;top:101px;width:231px"></div>
  <div class="side-title" style="top:115px">FOLLOW ON</div>
  <div class="socials">
    <span style="background:#2d5597" aria-label="Social profile 1"></span>
    <span style="background:#3aa3dd" aria-label="Social profile 2"></span>
    <span style="background:#1e5f8e" aria-label="Social profile 3"></span>
    <span style="background:#f2b63a" aria-label="Email us"><svg width="11" height="8" viewBox="0 0 11 8" aria-hidden="true"><rect x=".5" y=".5" width="10" height="7" fill="#fff"/><path d="M.5 .5l5 4 5-4" fill="none" stroke="#f2b63a"/></svg></span>
  </div>
  <div class="rule" style="left:584px;top:177px;width:231px"></div>
  <div class="side-title" style="top:202px">NEWSLETTER SIGNUP</div>
  <div class="newsletter">Email Address
    <span class="go"><svg width="10" height="10" viewBox="0 0 10 10" aria-hidden="true"><path d="M1 5h7M5 2l3 3-3 3" stroke="#fff" stroke-width="1.8" fill="none"/></svg></span>
  </div>

  <div class="rule" style="left:84px;top:155px;width:480px"></div>
  <div class="links" style="left:83px">
    <h3>SERVICES</h3>
    <ul><li>› Lorem ipsum dolor sit amet</li><li>› consectetur adipiscing elit</li><li>› Morbi et elit ut diam bibendum</li><li>› Dictum eget ut nisi</li></ul>
  </div>
  <div class="links" style="left:260px">
    <h3>QUICK LINKS</h3>
    <ul><li>› Morbi et elit ut diam bibendum</li><li>› Dictum eget ut nisi</li><li>› Lorem ipsum dolor sit amet</li><li>› consectetur adipiscing elit</li></ul>
  </div>
  <div class="links" style="left:419px">
    <h3>COMPANY</h3>
    <ul><li>› Dictum eget ut nisi</li><li>› Lorem ipsum dolor sit amet</li><li>› consectetur adipiscing elit</li><li>› Morbi et elit ut diam bibendum</li></ul>
  </div>
</section>

<footer class="site-footer">
  <div class="copy">Copyright©2015 SkyvoTrade. All rights reserved</div>
  <div class="legal">Privacy Policy &nbsp;|&nbsp; Sitemap</div>
</footer>

</body>
</html>
```